Shipping and Logistics, Project

Project description : Company Profile

A total logistics company covering domestic / international freight forwarding, warehouse management services, haulage, supply chain management, transport management & distribution, procurement & assembly services, shipping, chartering & bunker services, project logistics & tax exemption consultancy, oil & gas logistics, halal logistics services & integrated logistics management. We’re a well-established and experienced freight forwarder in Kuala Lumpur, Malaysia. We specialize in customized value-added solution that optimizes your supply chain by trimming inventory, reducing logistics cost and enhancing your customer service levels.

As a member of the Worldwide Parcel and Carriage Alliance which comprise of 170 global freight agents in 80 countries that promotes great handling in cross-trade logistics and freighting. You could rely on our efficiency in handlings of export cargo (FCL, LCL, Bulk and Conventional) between our global network offices worldwide with a total scale of 10,000 groomed specialists in various logistics division working together to ensure delivery task meets with your expectation. With our dedicated qualified and experienced professionals, we are fully committed to serving our clients.

Our generic services are listed below for your reference:

• Air Freight
• Ocean Freight FCL & LCL
• Container Haulage
• Warehousing
• Transportation and Distribution within Malaysia and Thailand
• Cross-Border Road Line-hauls between Thailand, Malaysia, Singapore and Laos
• Customs Brokerage and Forwarding
• Project Cargo Freight Forwarding for setting up of new plants / factories and ad hoc heavy-lift
• Air-Sea-Road-Rail multi-modal options
• Import / Export / Storage / Documentation / Handling of DG / Hazmat
• Vessel and Aircraft Charters

Our Mission
Based on the motto “Quick, Reliable and Polite”, we are dedicated to upholding the following three points corporate philosophy:
1. Adhering to the principle that “the customer always comes first”.
2. Contributing to the development of the local community.
3. Making it our duty to be responsible and sincere.

Our Edge
• One-Stop Logistics Solutions
• Extensive Network Throughout Malaysia
• Highly Qualified and Experienced Pool of Professionals
• Comprehensive IT Solutions
• Innovative and Customer-focused Solutions
• Flexible and Consistent in Managing Exceptions
• Total Supply Chain Visibility

Target Market
1. We sell the logistics services to all the industry in Malaysia and Worldwide. (ONE Stop Logistics Solutions)

Competitor
1. TR Valmont
2. Corvessa Transport
3. Brandt + Loewe
4. FELRO
5. QTV
6. Routemarks
7. Ilto Logistics

Rules for Picking a Company Name
1. Unique and unforgettable
2. Avoid unusual spellings
3. Easy to pronounce and remember
4. Keep it simple
5. Make some sense
6. Give a clue

Rules for Picking a Company Logo
4. Keep it simple
5. Make some sense
6. Give a clue

1. Simplicity
2. Memorability
3. Originality
4. Modern Yet Timeless
5. Balance
6. Complementary
7. Versatility

Stationery Information
1. Company Name : ZENFreight Solutions Sdn Bhd
2. Company Registration : 2837165-W
3. Address : 42-08, Jalan Cempaka Indah 5, Taman Seri Bayu, 81300 Johor Bahru, Johor, Malaysia.
4. Name : Derek Tan
5. Position : Manager
6. Mobile No : (+6019) 4381907
7. Office No : (+607) 5218764
8. Fax No : Not Available
9. Email Address : derek.tan@zenfreight-solutions.example
10. Web Domain : www.zenfreight-solutions.example
11. Company Slogan : ALWAYS ON THE MOVE

Target Market(s)

Corporate Company

Industry/Entity Type

Shipping and Logistics Industry

Requirements
Must have
• Company Full Name : ZENFREIGHT SOLUTIONS SDN. BHD.
Nice to have
• Keep it simple and unforgettable ...

```html
<!DOCTYPE html>
<html lang="en">
<head>
<meta charset="utf-8">
<title>ZENFreight Solutions – Stationery</title>
<link href="https://fonts.googleapis.com/css2?family=Poppins:wght@400;500&display=swap" rel="stylesheet">
<style>
  :root{
    --backdrop:#c8c8c8;
    --paper:#ffffff;
    --brand-blue:#3d89c9;
    --ink:#222222;
    --watermark:#efefef;
    --divider:#cfcfcf;
  }
  *{margin:0;padding:0;box-sizing:border-box}
  html,body{width:1200px;height:900px;overflow:hidden}
  body{background:var(--backdrop);font-family:"Poppins",sans-serif;color:var(--ink);position:relative}
  .sheet{position:absolute;background:var(--paper);overflow:hidden}
  .flaps{position:absolute;left:0;top:0;width:1200px;height:900px}
  .flap{fill:var(--brand-blue)}
  .watermark{position:absolute;border-radius:50%;background:var(--watermark)}
  .brand{position:absolute;display:flex;align-items:center;color:var(--brand-blue);font-weight:500}
  .brand-square{background:var(--brand-blue);flex:none}
  .brand-name{display:flex;flex-direction:column;line-height:1}
  .brand-sub{letter-spacing:.18em;white-space:nowrap}
  .rule{position:absolute;height:1px;background:var(--brand-blue)}
  .address-line{position:absolute;font-size:5.4px;text-align:center;color:var(--ink);white-space:nowrap}

  /* Cover sheet */
  .cover{left:114px;top:145px;width:314px;height:436px}
  .cover .brand{right:27px;top:22px;gap:8px}
  .cover .brand-square{width:26px;height:26px}
  .cover .brand-main{font-size:17px}
  .cover .brand-sub{font-size:6.6px;margin-top:4px}
  .cover .watermark{left:47px;top:130px;width:220px;height:220px}
  .slogan{position:absolute;left:26px;width:259px;top:405px;display:flex;align-items:center;gap:4px;color:var(--brand-blue);font-size:8.6px;letter-spacing:.16em;white-space:nowrap}
  .slogan::before,.slogan::after{content:"";flex:1;height:1px;background:var(--brand-blue)}

  /* Letterhead */
  .letterhead{left:460px;top:154px;width:291px;height:425px}
  .letterhead .brand{left:24px;top:13px;gap:5px}
  .letterhead .brand-square{width:18px;height:18px}
  .letterhead .brand-main{font-size:11px}
  .letterhead .brand-sub{font-size:4.4px;margin-top:3px}
  .letterhead .tagline{position:absolute;left:56px;top:40px;font-size:4.4px;color:var(--brand-blue);font-weight:500;white-space:nowrap}
  .contact{position:absolute;left:172px;top:14px;padding-left:6px;border-left:1px solid var(--divider);font-size:4.9px;line-height:6.1px;white-space:nowrap}
  .contact b{color:var(--brand-blue);font-weight:500}
  .contact .reg{margin-top:3px}
  .contact .accent{color:var(--brand-blue)}
  .letterhead .watermark{left:32px;top:123px;width:210px;height:210px}
  .letterhead .rule{left:23px;width:250px;top:401px}
  .letterhead .address-line{left:0;width:291px;top:406px}

  /* Large envelope */
  .envelope-large{left:786px;top:151px;width:308px;height:431px}
  .envelope-large .brand{left:25px;top:38px;gap:5px}
  .envelope-large .brand-square{width:18px;height:18px}
  .envelope-large .brand-main{font-size:10px}
  .envelope-large .brand-sub{font-size:4.3px;margin-top:3px}
  .envelope-large .watermark{left:39px;top:115px;width:230px;height:230px}
  .envelope-large .rule{left:28px;width:247px;top:406px}
  .envelope-large .address-line{left:0;width:308px;top:410px}

  /* DL envelope */
  .envelope-dl{left:436px;top:650px;width:340px;height:170px}
  .envelope-dl .brand{left:17px;top:22px;gap:5px}
  .envelope-dl .brand-square{width:16px;height:16px}
  .envelope-dl .brand-main{font-size:9px}
  .envelope-dl .brand-sub{font-size:3.8px;margin-top:2px}
  .envelope-dl .watermark{left:193px;top:37px;width:124px;height:124px}
  .return-address{position:absolute;left:19px;top:137px;font-size:5.6px;line-height:6.5px}
</style>
</head>
<body>
  <svg class="flaps" viewBox="0 0 1200 900" aria-hidden="true">
    <polygon class="flap" points="786,147 818,94 1055,94 1093,146 1093,154 786,151"/>
    <polygon class="flap" points="436,650 451,624 758,624 776,650"/>
  </svg>

  <section class="sheet cover">
    <div class="brand">
      <span class="brand-square"></span>
      <span class="brand-name"><span class="brand-main">ZENFREIGHT</span><span class="brand-sub">SOLUTIONS SDN. BHD.</span></span>
    </div>
    <div class="watermark" role="img" aria-label="Faint brand emblem"></div>
    <p class="slogan">ALWAYS ON THE MOVE</p>
  </section>

  <section class="sheet letterhead">
    <div class="brand">
      <span class="brand-square"></span>
      <span class="brand-name"><span class="brand-main">ZENFREIGHT</span><span class="brand-sub">SOLUTIONS SDN. BHD.</span></span>
    </div>
    <p class="tagline">ALWAYS ON THE MOVE</p>
    <div class="contact">
      <p><b>P:</b> (+6019) 438 1907</p>
      <p><b>M:</b> (+607) 521 8764</p>
      <p><b>E:</b> derek.tan@zenfreight-solutions.example</p>
      <p>www.<span class="accent">zenfreight-solutions</span>.example</p>
      <p class="reg">Company No. <span class="accent">2837165-W</span></p>
    </div>
    <div class="watermark" role="img" aria-label="Faint brand emblem"></div>
    <div class="rule"></div>
    <p class="address-line">42-08, Jalan Cempaka Indah 5, Taman Seri Bayu, 81300 Johor Bahru, Johor, Malaysia.</p>
  </section>

  <section class="sheet envelope-large">
    <div class="brand">
      <span class="brand-square"></span>
      <span class="brand-name"><span class="brand-main">ZENFREIGHT</span><span class="brand-sub">SOLUTIONS SDN. BHD.</span></span>
    </div>
    <div class="watermark" role="img" aria-label="Faint brand emblem"></div>
    <div class="rule"></div>
    <p class="address-line">42-08, Jalan Cempaka Indah 5, Taman Seri Bayu, 81300 Johor Bahru, Johor, Malaysia.</p>
  </section>

  <section class="sheet envelope-dl">
    <div class="brand">
      <span class="brand-square"></span>
      <span class="brand-name"><span class="brand-main">ZENFREIGHT</span><span class="brand-sub">SOLUTIONS SDN. BHD.</span></span>
    </div>
    <div class="watermark" role="img" aria-label="Faint brand emblem"></div>
    <p class="return-address">42-08, Jalan Cempaka Indah 5,<br>Taman Seri Bayu, 81300 Johor<br>Bahru, Johor, Malaysia.</p>
  </section>
</body>
</html>
```